Birchline Septic Solutions

Would like to see some single sided ones but would also like to see some double sided with one sided only being the logo. Owners name is Colin Vandro. Phone number is 555-214-0387
Services are pumping, inspections, installs, and repairs

Contact Information for Business Card

555-241-0387 Colin Vandro Alderton, OH

```html
<!DOCTYPE html>
<html lang="en">
<head>
<meta charset="utf-8">
<title>Birchline Septic Solutions – Business Cards</title>
<link rel="stylesheet" href="https://fonts.googleapis.com/css2?family=Open+Sans:wght@400;600;700;800&display=swap">
<style>
  :root {
    --page-bg: #1f1f21;
    --card-bg: #232327;
    --card-emboss: #151518;
    --ink-white: #f4f4f4;
    --accent-teal: #2bbdb4;
    --scenery-dark: #111113;
  }
  * { box-sizing: border-box; margin: 0; padding: 0; }
  html, body {
    width: 1200px; height: 779px; overflow: hidden;
    background: var(--page-bg);
    font-family: "Open Sans", Arial, sans-serif;
  }
  .sheet {
    position: relative; width: 1200px; height: 779px;
    display: flex; align-items: center; justify-content: center; gap: 40px;
  }
  .card {
    position: relative; width: 540px; height: 309px;
    background: var(--card-bg); overflow: hidden;
    box-shadow: 0 14px 30px rgba(0,0,0,.55);
  }

  /* Back side: name only */
  .card-back { display: flex; align-items: center; justify-content: center; }
  .back-wordmark {
    display: flex; flex-direction: column; align-items: center;
    color: var(--card-emboss); font-weight: 800; text-transform: uppercase;
    line-height: 1;
  }
  .back-wordmark .wordmark-main { font-size: 58px; letter-spacing: 2px; }
  .back-wordmark .wordmark-sub { font-size: 19px; letter-spacing: 9px; margin-top: 10px; }

  /* Front side */
  .scenery-area {
    position: absolute; left: 0; top: 0; width: 140px; height: 309px;
    background: linear-gradient(90deg, var(--scenery-dark) 0%, var(--card-bg) 100%);
  }
  .front-wordmark {
    position: absolute; right: 34px; top: 36px;
    display: flex; flex-direction: column; align-items: flex-end;
    color: var(--ink-white); font-weight: 800; text-transform: uppercase; line-height: 1;
  }
  .front-wordmark .wordmark-main { font-size: 40px; letter-spacing: 1px; }
  .front-wordmark .wordmark-sub { font-size: 13px; letter-spacing: 6px; margin-top: 7px; }

  .contact {
    position: absolute; right: 34px; top: 122px;
    display: flex; align-items: stretch; gap: 12px;
  }
  .contact-text { text-align: right; color: var(--ink-white); }
  .owner-name { font-size: 24px; font-weight: 700; line-height: 1.1; }
  .owner-first { color: var(--accent-teal); }
  .owner-last { color: var(--ink-white); }
  .location, .phone { font-size: 13px; font-weight: 600; line-height: 1.45; }
  .phone { display: flex; align-items: center; justify-content: flex-end; gap: 6px; }
  .phone svg { width: 12px; height: 12px; fill: var(--accent-teal); }
  .accent-bar { width: 7px; background: var(--accent-teal); }

  .services {
    position: absolute; left: 150px; right: 24px; bottom: 30px;
    display: flex; flex-direction: column; align-items: center; gap: 8px;
  }
  .services-label {
    background: var(--accent-teal); color: var(--ink-white);
    font-size: 12px; font-weight: 700; letter-spacing: .5px;
    padding: 3px 16px; border-radius: 50%;
  }
  .services-list { display: flex; gap: 12px; list-style: none; color: var(--ink-white); font-size: 13px; }
  .services-list li { display: flex; align-items: center; gap: 5px; white-space: nowrap; }
  .services-list li::before {
    content: ""; width: 8px; height: 8px; border-radius: 50%; background: var(--accent-teal);
  }
</style>
</head>
<body>
<main class="sheet">
  <section class="card card-back" aria-label="Card back">
    <div class="back-wordmark">
      <span class="wordmark-main">Birchline</span>
      <span class="wordmark-sub">Septic Solutions</span>
    </div>
  </section>

  <section class="card card-front" aria-label="Card front">
    <div class="scenery-area" role="img" aria-label="Dark glossy forest and mountain scenery along the left edge"></div>

    <div class="front-wordmark">
      <span class="wordmark-main">Birchline</span>
      <span class="wordmark-sub">Septic Solutions</span>
    </div>

    <div class="contact">
      <div class="contact-text">
        <p class="owner-name"><span class="owner-first">Colin</span> <span class="owner-last">Vandro</span></p>
        <p class="location">Alderton, OH</p>
        <p class="phone">555-241-0387
          <svg viewBox="0 0 24 24" aria-hidden="true"><path d="M6.6 10.8a15.1 15.1 0 0 0 6.6 6.6l2.2-2.2a1 1 0 0 1 1-.25 11.4 11.4 0 0 0 3.6.57 1 1 0 0 1 1 1V20a1 1 0 0 1-1 1A17 17 0 0 1 3 4a1 1 0 0 1 1-1h3.5a1 1 0 0 1 1 1c0 1.25.2 2.45.57 3.57a1 1 0 0 1-.25 1z"/></svg>
        </p>
      </div>
      <div class="accent-bar"></div>
    </div>

    <div class="services">
      <span class="services-label">SERVICES</span>
      <ul class="services-list">
        <li>Pumping</li>
        <li>Inspections</li>
        <li>Installs</li>
        <li>And Repairs</li>
      </ul>
    </div>
  </section>
</main>
</body>
</html>
```